RTavenor Business Cards & Letterhead

I have a logo but need a design for some new business cards. We are a Design-Build Firm that specializes in the design and construction of commercial projects.
the cards need to be professional. no cartoon stuff.
i would like to have the cards in AI format so I can update the card as needed. Logo is provided.
Our Address is: 4187 Marlowe Ct. Apex, North Carolina 27614

```html
<!DOCTYPE html>
<html lang="en">
<head>
<meta charset="utf-8">
<title>RTavenor Business Card</title>
<link rel="stylesheet" href="https://fonts.googleapis.com/css2?family=Open+Sans:wght@400;700;800&display=swap">
<style>
  :root {
    --bg: #4a4a4a;
    --card-white: #ffffff;
    --brand-blue: #0a5fa6;
    --brand-deep: #004a7c;
    --brand-light: #0a80c0;
    --ink: #2a2a2a;
  }
  * { box-sizing: border-box; margin: 0; padding: 0; }
  html, body { width: 1200px; height: 801px; overflow: hidden; }
  body {
    background: var(--bg);
    font-family: "Open Sans", Arial, sans-serif;
    position: relative;
  }
  .card {
    position: absolute;
    top: 252px;
    width: 520px;
    height: 297px;
    border-radius: 16px;
    overflow: hidden;
  }
  .card-front { left: 50px; background: var(--card-white); }
  .card-back {
    left: 630px;
    background: linear-gradient(120deg, var(--brand-deep) 0%, #005a94 45%, var(--brand-light) 100%);
  }
  .identity {
    position: absolute;
    right: 208px;
    top: 96px;
    text-align: right;
  }
  .person-name {
    font-weight: 700;
    font-size: 23px;
    letter-spacing: 0.5px;
    color: var(--brand-blue);
    text-transform: uppercase;
    line-height: 1.1;
  }
  .person-title {
    font-size: 15px;
    color: var(--ink);
    letter-spacing: 0.4px;
  }
  .divider {
    position: absolute;
    left: 322px;
    top: 82px;
    width: 1.5px;
    height: 72px;
    background: var(--brand-blue);
  }
  .contacts {
    position: absolute;
    left: 334px;
    top: 80px;
    list-style: none;
    font-size: 14px;
    color: var(--ink);
    line-height: 25px;
    letter-spacing: 0.3px;
  }
  .contacts li { display: flex; align-items: center; gap: 6px; white-space: nowrap; }
  .contacts svg { width: 12px; height: 12px; fill: var(--brand-blue); flex: none; }
  .address-band {
    position: absolute;
    left: 0;
    right: 0;
    bottom: 18px;
    height: 26px;
    background: linear-gradient(90deg, var(--brand-deep), var(--brand-blue) 50%, var(--brand-deep));
    color: #ffffff;
    font-size: 14px;
    line-height: 26px;
    padding-left: 160px;
    letter-spacing: 0.3px;
    white-space: nowrap;
  }
  .brand-lockup {
    position: absolute;
    left: 0;
    right: 0;
    top: 112px;
    display: flex;
    justify-content: center;
    align-items: center;
    gap: 14px;
  }
  .brand-mark { width: 40px; height: 40px; background: #ffffff; }
  .brand-name {
    font-weight: 800;
    font-size: 54px;
    color: #ffffff;
    letter-spacing: 1px;
    line-height: 1;
  }
</style>
</head>
<body>
  <section class="card card-front" aria-label="Business card front">
    <div class="identity">
      <h1 class="person-name">Owen Marsh</h1>
      <p class="person-title">Managing Director</p>
    </div>
    <span class="divider"></span>
    <ul class="contacts">
      <li>
        <svg viewBox="0 0 24 24" aria-hidden="true"><path d="M6.6 10.8a15.1 15.1 0 0 0 6.6 6.6l2.2-2.2a1 1 0 0 1 1-.25 11.4 11.4 0 0 0 3.6.57 1 1 0 0 1 1 1V20a1 1 0 0 1-1 1A17 17 0 0 1 3 4a1 1 0 0 1 1-1h3.5a1 1 0 0 1 1 1c0 1.25.2 2.45.57 3.57a1 1 0 0 1-.25 1z"/></svg>
        555 284 316
      </li>
      <li>
        <svg viewBox="0 0 24 24" aria-hidden="true"><path d="M2 5h20v2l-10 7L2 7z M2 9l10 7 10-7v10H2z"/></svg>
        info@rtavenor.net
      </li>
      <li>
        <svg viewBox="0 0 24 24" aria-hidden="true"><circle cx="12" cy="12" r="10"/></svg>
        www.rtavenorbuild.net
      </li>
    </ul>
    <div class="address-band">4187 Marlowe Ct. Fenwick,South Carrow 27614</div>
  </section>

  <section class="card card-back" aria-label="Business card back">
    <div class="brand-lockup">
      <span class="brand-mark"></span>
      <span class="brand-name">RTAVENOR</span>
    </div>
  </section>
</body>
</html>
```